Corvane Systems Web Site

Need a complete redesign of the website to make it cleaner and up to date.
Current website: http://www.corvanesystems.example/
I am looking for a single page design focused on giving all the information about the POC (Pump Off Controller). And highlighting its benefits: Increased oil production, quick ROI, ease of use and low maintenance cost.
Here's a presentation of the product:
http://slidewharf.example/qk4mtz8vn2ra/?utm_campaign=share&utm_medium=copy&rc=ex0share
Please consider participating on the flyer design:
http://jobs.artmarket.example/job.aspx?id=391726
Here are some design examples of web sites I like:
http://www.bright-harbor.example/
I just added the source files for our business cards. I would like to see designs that incorporate the "tag cloud" on the back of the card..
Target Market(s)
Oil field decision makers. Engineers and technicians from 20 to 60.
Investors and venture capitalists.
Industry/Entity Type
Cleaner
Requirements
Must have
- Single page design
Nice to have
- Responsive web design

```html
<!DOCTYPE html>
<html lang="en">
<head>
<meta charset="utf-8">
<title>Corvane Systems – Smart Pump-Off Controller</title>
<link href="https://fonts.googleapis.com/css2?family=Roboto+Condensed:wght@400;500;700&family=Roboto:wght@300;400&display=swap" rel="stylesheet">
<style>
:root{
  --red:#c0101c;
  --red-dark:#a00a14;
  --yellow:#f2d21a;
  --cream:#ffe7b0;
  --ink:#2b2b2b;
  --muted:#8c8c8c;
  --panel:#efefef;
  --panel-line:#dcdcdc;
  --footer:#474747;
  --footer-text:#c4c4c4;
}
*{margin:0;padding:0;box-sizing:border-box}
html,body{width:764px;height:1200px;overflow:hidden;background:#fff}
body{position:relative;font-family:"Roboto Condensed",Arial,sans-serif;color:var(--ink)}
h1,h2,h3,p{font-weight:400}
.abs{position:absolute}
.body-copy{font-family:Roboto,Arial,sans-serif;font-size:7px;line-height:13px;color:var(--muted)}

/* header */
.site-header{left:0;top:0;width:764px;height:53px;background:var(--red)}
.brand{left:110px;top:19px;display:flex;align-items:center;gap:5px;color:#fff;font-weight:700;font-size:13px;letter-spacing:.5px}
.brand-dot{width:12px;height:12px;border-radius:50%;background:#fff}
.main-nav{top:23px;color:#fff;font-size:9px;font-weight:500}

/* hero */
.hero{left:0;top:53px;width:764px;height:334px;
  background:
    radial-gradient(ellipse 260px 120px at 560px 250px,rgba(255,214,140,.55),rgba(255,214,140,0) 70%),
    linear-gradient(100deg,rgba(40,30,22,.75) 0%,rgba(40,30,22,0) 40%),
    linear-gradient(180deg,#6d6660 0%,#8a7b6a 35%,#b58c55 58%,#6a5948 78%,#2e2926 100%)}
.hero-chev{top:190px}
.hero-title{left:109px;top:247px;color:#fff;font-size:16px;font-weight:700}
.hero-sub{left:110px;top:272px;color:var(--yellow);font-size:13.5px;line-height:21.5px}
.hero-arrows{left:622px;top:328px;width:32px;height:16px;background:var(--red)}

/* benefits band */
.benefits{left:109px;top:344px;width:545px;height:154px;background:var(--red)}
.benefit-photo{top:358px;width:163px;height:91px}
.benefit-cap{top:457px;color:var(--cream);font-size:9px;font-weight:500;line-height:13.5px;width:165px}

/* why smart */
.section-title{font-size:11.5px;font-weight:500;color:#333}
.rule-red{left:109px;top:543px;width:282px;height:1.5px;background:var(--red)}
.chart-thumb{width:105px;height:72px;background:#ececec;border:1px solid #d6d6d6}
.item-title{font-family:Roboto,Arial,sans-serif;font-size:9px;color:#333}
.rule-grey{left:109px;top:644px;width:282px;height:1px;background:#e0e0e0}

/* pumping panels */
.pump-head{left:428px;top:524px;font-size:8.5px;line-height:15px;color:#444}
.pump-panel{left:426px;width:228px;height:73px;background:var(--panel);border:1px solid var(--panel-line)}
.pump-label{color:var(--red);font-size:8.5px;font-weight:500}
.track{height:10px;border-radius:5px;background:#222}
.fill{position:absolute;left:0;top:0;bottom:0;border-radius:5px}
.tick{width:1px;height:4px;background:#999}
.tick-label{font-family:Roboto,Arial,sans-serif;font-size:6.5px;color:#666}

/* connectivity banner */
.connect{left:109px;top:753px;width:545px;height:102px;
  background:
    radial-gradient(ellipse 130px 50px at 120px 35px,rgba(255,255,255,.9),rgba(255,255,255,0) 75%),
    linear-gradient(90deg,#bdbdbd 0%,#5d5d5d 30%,#151515 46%,#0a0a0a 100%)}
.connect-text{left:338px;top:771px;color:#fff;font-size:11.5px;font-weight:500}
.connect-em{left:338px;top:786px;color:#d5131f;font-size:15px;font-weight:700}
.btn{display:flex;align-items:center;justify-content:center;background:linear-gradient(180deg,#e0202b,var(--red-dark));color:#fff;font-size:8.5px;border-radius:2px}

/* columns */
.col-photo{top:909px;width:160px;height:97px}
.col-text{top:1014px;width:164px;font-size:7.4px;line-height:14.4px}

/* footer */
.site-footer{left:0;top:1141px;width:764px;height:59px;background:var(--footer)}
.foot-nav{left:109px;top:1159px;font-size:6.5px;color:var(--footer-text);font-family:Roboto,Arial,sans-serif}
.copyright{left:109px;top:1177px;font-size:6px;color:var(--footer-text);font-family:Roboto,Arial,sans-serif}
.social{top:1161px;width:17px;height:17px;border-radius:50%;background:#6a6a6a}
</style>
</head>
<body>

<header class="abs site-header">
  <div class="abs brand"><span class="brand-dot"></span>CORVANE</div>
  <nav>
    <span class="abs main-nav" style="left:301px">HOME</span>
    <span class="abs main-nav" style="left:362px">COMPANY</span>
    <span class="abs main-nav" style="left:438px">RODUCTSE</span>
    <span class="abs main-nav" style="left:517px">TELEMETRYE</span>
    <span class="abs main-nav" style="left:604px">CONTACT US</span>
  </nav>
</header>

<section class="abs hero" role="img" aria-label="Offshore oil platform at sunset seen from a steel walkway"></section>
<svg class="abs hero-chev" style="left:36px" width="16" height="48" viewBox="0 0 16 48"><path d="M14 2 2 24 14 46" stroke="rgba(255,255,255,.35)" stroke-width="1.2" fill="none"/></svg>
<svg class="abs hero-chev" style="left:710px" width="16" height="48" viewBox="0 0 16 48"><path d="M2 2 14 24 2 46" stroke="rgba(255,255,255,.35)" stroke-width="1.2" fill="none"/></svg>
<h1 class="abs hero-title">SMART PUMP -OFF CONTROLLER(POC)</h1>
<p class="abs hero-sub">INCREASED OIL PRODUCTION, QUICK ROI, EASE OF USE<br>AND LOW MAINTENANCE COST.</p>
<div class="abs hero-arrows">
  <svg width="32" height="16" viewBox="0 0 32 16"><path d="M10 5 7 8 10 11M22 5 25 8 22 11" stroke="#fff" stroke-width="1.2" fill="none"/><line x1="16" y1="0" x2="16" y2="16" stroke="#a00a14"/></svg>
</div>

<section class="abs benefits"></section>
<div class="abs benefit-photo" style="left:123px;background:radial-gradient(ellipse 60px 30px at 40px 80px,#ffd27a,rgba(255,210,122,0) 80%),linear-gradient(180deg,#5a2a22,#c9572a 62%,#2a1410)" role="img" aria-label="Pumpjack silhouette against sunset"></div>
<div class="abs benefit-photo" style="left:301px;background:radial-gradient(ellipse 90px 70px at 50% 55%,#efe6cf,#cdbf9f 60%,#5a4f40)" role="img" aria-label="Close-up of a meter dial"></div>
<div class="abs benefit-photo" style="left:478px;background:linear-gradient(135deg,#5c6670,#8a8f93 45%,#6d6a62 65%,#3c3f44)" role="img" aria-label="Field technician in safety gear at a plant"></div>
<p class="abs benefit-cap" style="left:123px">HIGH RELIABILITY AND ACCESSIBILITY</p>
<p class="abs benefit-cap" style="left:301px">ALARM GENERATION AND REPORTING</p>
<p class="abs benefit-cap" style="left:478px">COST SAVINGS DUE TO IMPROVED PUMPER EFFICIENCY.</p>

<h2 class="abs section-title" style="left:109px;top:522px">WHY SMART ?</h2>
<div class="abs rule-red"></div>

<svg class="abs chart-thumb" style="left:109px;top:560px" viewBox="0 0 105 72" role="img" aria-label="Load versus position chart">
  <rect x="17" y="4" width="86" height="58" fill="#111a11"/>
  <g stroke="#2c4a2c" stroke-width=".5">
    <path d="M17 15H103M17 26H103M17 37H103M17 48H103M34 4V62M51 4V62M68 4V62M85 4V62"/>
  </g>
  <path d="M22 36C35 28 50 30 64 25 78 20 92 26 98 30 88 38 74 42 60 40 46 38 34 46 22 36Z" stroke="#d9d9d9" stroke-width=".8" fill="none"/>
  <g font-family="Roboto,Arial,sans-serif" font-size="5" fill="#333">
    <text x="2" y="8">3200</text><text x="2" y="19">3000</text><text x="2" y="30">2800</text><text x="2" y="41">2600</text><text x="2" y="52">2400</text><text x="2" y="62">2200</text>
    <text x="14" y="69">1400</text><text x="34" y="69">1600</text><text x="53" y="69">1800</text><text x="71" y="69">2000</text><text x="89" y="69">2200</text>
  </g>
</svg>
<h3 class="abs item-title" style="left:234px;top:563px">SELF ADJUSTING ALGORITJM</h3>
<p class="abs body-copy" style="left:234px;top:580px;width:160px">Corvane automatically controls the on-off condition of the well through its continuous self adjusting software.</p>
<div class="abs rule-grey"></div>
<svg class="abs chart-thumb" style="left:109px;top:656px" viewBox="0 0 105 72" role="img" aria-label="Load versus position chart">
  <rect x="17" y="4" width="86" height="58" fill="#111a11"/>
  <g stroke="#2c4a2c" stroke-width=".5">
    <path d="M17 15H103M17 26H103M17 37H103M17 48H103M34 4V62M51 4V62M68 4V62M85 4V62"/>
  </g>
  <path d="M24 34C36 27 56 26 72 27 86 28 94 31 96 33 90 39 74 40 58 38 42 37 30 42 24 34Z" stroke="#d9d9d9" stroke-width=".8" fill="none"/>
  <g font-family="Roboto,Arial,sans-serif" font-size="5" fill="#333">
    <text x="2" y="19">3200</text><text x="2" y="30">3000</text><text x="2" y="41">2800</text><text x="2" y="52">2600</text><text x="2" y="62">2400</text>
    <text x="14" y="69">1400</text><text x="38" y="69">1600</text><text x="61" y="69">1800</text><text x="84" y="69">2000</text>
  </g>
</svg>
<h3 class="abs item-title" style="left:234px;top:659px">MAXIMUM PUMP EFFICIENCY</h3>
<p class="abs body-copy" style="left:234px;top:676px;width:160px">Corvane automatically controls the on-off condition of the well through its continuous self adjusting software.</p>

<p class="abs pump-head">OVER PUMPING AND UNDER PUMPING CONDITIONS BY TIMES<br>(BASED) AN A 15 MIN TIMER)</p>

<div class="abs pump-panel" style="top:565px">
  <div class="abs pump-label" style="left:14px;top:11px">OVER PUMPING CONDITIONS</div>
  <div class="abs track" style="left:14px;top:33px;width:202px">
    <div class="fill" style="width:80px;background:linear-gradient(180deg,#ff3a46,#b3101a)"></div>
    <div class="abs" style="left:75px;top:-1px;width:12px;height:12px;border-radius:50%;background:#ccc;border:1px solid #888"></div>
  </div>
  <span class="abs tick" style="left:55px;top:46px"></span>
  <span class="abs tick" style="left:158px;top:46px"></span>
  <span class="abs tick-label" style="left:18px;top:51px">PUMP FLUID CONDITION</span>
  <span class="abs tick-label" style="left:125px;top:51px">PUMP OFF CONDITION</span>
</div>

<div class="abs pump-panel" style="top:648px">
  <div class="abs pump-label" style="left:14px;top:11px">UNDER PUMPING CONDITIONS</div>
  <div class="abs" style="left:112px;top:24px;width:26px;height:11px;background:#111;color:#fff;font-size:6.5px;display:flex;align-items:center;justify-content:center;font-family:Roboto,Arial,sans-serif">60%</div>
  <div class="abs track" style="left:14px;top:36px;width:204px">
    <div class="fill" style="width:110px;background:linear-gradient(90deg,#d2283c,#c24fc8)"></div>
  </div>
  <span class="abs tick" style="left:55px;top:50px"></span>
  <span class="abs tick-label" style="left:16px;top:57px">PUMPING &nbsp;FLUID CONDITION</span>
</div>

<section class="abs connect" role="img" aria-label="Smartphone resting on a keyboard"></section>
<p class="abs connect-text">ACCESS TYOUR WELL STATUS FROM ANYWHERE WITH AN</p>
<p class="abs connect-em">INTERNET CONNECTION.</p>
<a class="abs btn" style="left:339px;top:811px;width:145px;height:24px">CLICK HERE FOR KNOW INFO</a>

<h2 class="abs section-title" style="left:109px;top:881px">RELIABLE AND DEPENDABLE</h2>
<h2 class="abs section-title" style="left:289px;top:881px">INNOVATION &amp; EMERGING</h2>
<h2 class="abs section-title" style="left:472px;top:881px">COMPANY</h2>

<div class="abs col-photo" style="left:109px;background:linear-gradient(135deg,#3b2a22,#b88a66 45%,#e6d8c6 75%,#f0ebe4)" role="img" aria-label="Business handshake"></div>
<div class="abs col-photo" style="left:289px;background:radial-gradient(ellipse 26px 34px at 67% 40%,#ffffff,rgba(255,255,255,0) 90%),linear-gradient(180deg,#1d3f5c,#2f6a95 70%,#4b90c4)" role="img" aria-label="Row of light bulbs with one lit"></div>

<p class="abs body-copy col-text" style="left:109px">The dynamic nature of the Oil Industry requires smart and innovative methods and tools in its quest to produce affordable energy. Similarly, companies must seek...</p>
<p class="abs body-copy col-text" style="left:289px">The dynamic nature of the Oil Industry requires smart and innovative methods and tools in its quest to produce affordable energy. Similarly, companies must seek...</p>

<h3 class="abs" style="left:472px;top:906px;color:var(--red);font-size:9px;font-weight:500">SMART PUMP -OFF CONTROLLER(POC)</h3>
<p class="abs body-copy" style="left:472px;top:925px;width:186px;font-size:6.5px">The dynamic nature of the Oil Industry requires smart and innovative methods and tools in its quest to produce affordable energy. Similarly, companies must seek cost-effectiveness and efficiency at every phase of production and distribution in order to stay competitive.</p>
<p class="abs body-copy" style="left:472px;top:1004px;width:186px;font-size:6.5px">Corvane Systems, Inc., is here to offer its ample experience in designing and manufacturing automated solutions to the beam pump control. Besides its line of smart Pump-Off Controllers (POC) solutions include local wireless technology, telemetry SCADA and internet connectivity.</p>

<a class="abs btn" style="left:110px;top:1082px;width:72px;height:22px">CLICK HERE</a>
<a class="abs btn" style="left:290px;top:1082px;width:72px;height:22px">CLICK HERE</a>
<a class="abs btn" style="left:470px;top:1082px;width:72px;height:22px">CLICK HERE</a>

<footer class="abs site-footer"></footer>
<p class="abs foot-nav">HOME &nbsp;&nbsp;&nbsp;| &nbsp;&nbsp;&nbsp;COMPANY &nbsp;&nbsp;&nbsp;| &nbsp;&nbsp;&nbsp;RODUCTSE &nbsp;&nbsp;&nbsp;| &nbsp;&nbsp;&nbsp;TELEMETRYE &nbsp;&nbsp;&nbsp;| &nbsp;&nbsp;&nbsp;CONTACT US</p>
<p class="abs copyright">COPYRIGHT © 2014. CORVANE. ALL RIGHTS RESERVED.</p>
<span class="abs social" style="left:564px"></span>
<span class="abs social" style="left:588px"></span>
<span class="abs social" style="left:612px"></span>
<span class="abs social" style="left:636px"></span>

</body>
</html>
```